ORIM Holding

ORIM holding is located in the UAE. In the company, there are several departments covering Hospitality management, Facility Management, interior design and Construction.

The logo should not include the name holding, Just ORIM.

Needed Items:

(1) Logo.
(2) Business Card.
(3) Letterhead
(4) Envelope
(5) cd cover
(6) email signature
Updates

The previous brief was misplaced with another competition. Current update is the final.

Target Market(s)

Collaboration with international high end firms.

Industry/Entity Type

Business

Requirements
Must have
• COLOR PREFERENCE Maximum 2 colors, preferably mono-color with different shades.
Nice to have
• Elegant, luxurious, and minimalistic.

```html
<!DOCTYPE html>
<html lang="en">
<head>
<meta charset="utf-8">
<title>ORIM Holding – Business Card</title>
<link href="https://fonts.googleapis.com/css2?family=Michroma&family=Arimo:wght@400&display=swap" rel="stylesheet">
<style>
  :root {
    --backdrop: #2b2c2e;
    --card: #1c1d20;
    --brand-blue: #1a86d6;
    --text-grey: #b4b4b4;
    --rule-grey: #6a6a6a;
    --pattern-light: #8e8e90;
    --pattern-dark: #141416;
  }
  * { margin: 0; padding: 0; box-sizing: border-box; }
  html, body { width: 1200px; height: 1108px; overflow: hidden; background: var(--backdrop); }
  .canvas { position: relative; width: 1200px; height: 1108px; }

  .card {
    position: absolute;
    width: 380px;
    height: 620px;
    border-radius: 22px;
    background: var(--card);
    overflow: hidden;
  }
  .card--front { left: 170px; top: 244px; }
  .card--back { left: 650px; top: 244px; }

  /* Front */
  .wordmark {
    position: absolute;
    top: 120px; left: 0; right: 0;
    text-align: center;
    font-family: "Michroma", sans-serif;
    font-size: 74px;
    letter-spacing: 4px;
    color: var(--brand-blue);
  }
  .identity { position: absolute; top: 318px; left: 0; right: 0; text-align: center; }
  .identity__name {
    font-family: "Michroma", sans-serif;
    font-size: 24px;
    letter-spacing: 1px;
    color: var(--brand-blue);
  }
  .identity__title {
    margin-top: 4px;
    font-family: "Arimo", sans-serif;
    font-size: 19px;
    color: var(--text-grey);
  }
  .contact-icons {
    position: absolute; top: 400px; left: 40px; right: 40px;
    display: flex; align-items: center; gap: 8px;
  }
  .contact-icons__rule { flex: 1; height: 1px; background: var(--rule-grey); }
  .contact-icons__tile {
    width: 30px; height: 30px; border-radius: 4px;
    background: var(--brand-blue);
    display: flex; align-items: center; justify-content: center;
  }
  .contact-list {
    position: absolute; top: 446px; left: 0; right: 0;
    text-align: center;
    font-family: "Arimo", sans-serif;
    font-size: 19px; line-height: 27px;
    color: var(--text-grey);
  }
  .contact-divider {
    position: absolute; top: 537px; left: 72px; right: 72px;
    height: 1px; background: var(--rule-grey);
  }
  .address {
    position: absolute; top: 548px; left: 0; right: 0;
    text-align: center;
    font-family: "Arimo", sans-serif;
    font-size: 19px; line-height: 26px;
    color: var(--text-grey);
  }

  /* Back */
  .back-pattern {
    position: absolute; inset: 0;
    background: linear-gradient(160deg, var(--pattern-light) 0%, #4a4b4e 30%, #26272a 55%, var(--pattern-dark) 100%);
    opacity: 0.55;
  }
  .back-wordmark {
    position: absolute; right: 42px; bottom: 150px;
    font-family: "Michroma", sans-serif;
    font-size: 28px; letter-spacing: 2px;
    color: var(--brand-blue);
  }
</style>
</head>
<body>
<main class="canvas">
  <section class="card card--front" aria-label="Business card front">
    <div class="wordmark">ORIM</div>
    <div class="identity">
      <p class="identity__name">DANIEL HARPER</p>
      <p class="identity__title">Managing Director</p>
    </div>
    <div class="contact-icons">
      <span class="contact-icons__rule"></span>
      <span class="contact-icons__tile" aria-label="Phone">
        <svg width="18" height="18" viewBox="0 0 24 24"><path d="M6.6 10.8a15 15 0 0 0 6.6 6.6l2.2-2.2a1 1 0 0 1 1-.25 11.4 11.4 0 0 0 3.6.57 1 1 0 0 1 1 1V20a1 1 0 0 1-1 1A17 17 0 0 1 3 4a1 1 0 0 1 1-1h3.5a1 1 0 0 1 1 1c0 1.25.2 2.45.57 3.57a1 1 0 0 1-.25 1z" fill="#1c1d20"/></svg>
      </span>
      <span class="contact-icons__tile" aria-label="Email">
        <svg width="18" height="18" viewBox="0 0 24 24"><rect x="3" y="6" width="18" height="12" fill="none" stroke="#1c1d20" stroke-width="2"/><path d="M3 6l9 7 9-7" fill="none" stroke="#1c1d20" stroke-width="2"/></svg>
      </span>
      <span class="contact-icons__tile" aria-label="Website">
        <svg width="18" height="18" viewBox="0 0 24 24"><circle cx="12" cy="12" r="8.5" fill="none" stroke="#1c1d20" stroke-width="2"/><path d="M3.5 12h17M12 3.5c3 3 3 14 0 17M12 3.5c-3 3-3 14 0 17" fill="none" stroke="#1c1d20" stroke-width="1.6"/></svg>
      </span>
      <span class="contact-icons__rule"></span>
    </div>
    <div class="contact-list">
      <p>044-555 010 234</p>
      <p>info@mailname.com</p>
      <p>www.orimsite.com</p>
    </div>
    <div class="contact-divider"></div>
    <div class="address">
      <p>88, Street line here</p>
      <p>10250,Country Name</p>
    </div>
  </section>

  <section class="card card--back" aria-label="Business card back">
    <div class="back-pattern" role="img" aria-label="Repeating brand-name pattern in glossy silver fading to black"></div>
    <div class="back-wordmark">ORIM</div>
  </section>
</main>
</body>
</html>
```